I need a business card design for a new business based in South West Australia.
I specialize in residential window cleaning & general handyman maintenance.

Dale Marsh - 412 SILVER HAWK DETAILING
- Window Cleaning
- House Maintenance

```html
<!DOCTYPE html>
<html lang="en">
<head>
<meta charset="utf-8">
<title>412 Silver Hawk Detailing – Business Card</title>
<link rel="stylesheet" href="https://fonts.googleapis.com/css2?family=Tinos:wght@400;700&family=Arimo:wght@400&display=swap">
<style>
  :root {
    --page-bg: #e9e7e3;
    --card-white: #ffffff;
    --card-shade: #eceeee;
    --band-blue-light: #c6d9ef;
    --band-blue: #a9c4e6;
    --art-top: #9aa29f;
    --art-bottom: #d6eed8;
    --ink: #111111;
  }
  html, body {
    margin: 0;
    padding: 0;
    width: 1200px;
    height: 892px;
    overflow: hidden;
    background: var(--page-bg);
  }
  .canvas {
    position: relative;
    width: 1200px;
    height: 892px;
    display: flex;
    align-items: center;
    justify-content: center;
  }
  .card {
    position: relative;
    width: 1000px;
    height: 572px;
    background: linear-gradient(180deg, var(--card-white) 55%, var(--card-shade) 100%);
    box-shadow: 0 10px 30px rgba(0,0,0,0.18);
    overflow: hidden;
  }
  .brand-band {
    position: absolute;
    left: 0; top: 0;
    width: 100%;
    height: 132px;
    background: linear-gradient(180deg, var(--band-blue-light), var(--band-blue));
    display: flex;
    align-items: center;
    justify-content: center;
  }
  .brand-name {
    margin: 0;
    font-family: "Tinos", "Times New Roman", serif;
    font-weight: 400;
    font-size: 50px;
    letter-spacing: 1px;
    color: var(--ink);
    white-space: nowrap;
  }
  .squeegee-art {
    position: absolute;
    left: 40px; right: 40px;
    top: 140px;
    height: 150px;
    background: linear-gradient(180deg, var(--art-top), var(--art-bottom));
  }
  .owner-name {
    position: absolute;
    left: 0; right: 0;
    top: 318px;
    margin: 0;
    text-align: center;
    font-family: "Tinos", "Times New Roman", serif;
    font-weight: 700;
    font-size: 66px;
    line-height: 1.1;
    color: var(--ink);
    white-space: nowrap;
  }
  .services {
    position: absolute;
    left: 40px; right: 40px;
    bottom: 40px;
    margin: 0;
    padding: 0;
    list-style: none;
    display: flex;
    justify-content: space-between;
  }
  .service {
    display: flex;
    align-items: center;
    gap: 22px;
    font-family: "Arimo", Arial, sans-serif;
    font-size: 36px;
    color: var(--ink);
    white-space: nowrap;
  }
  .service-icon { width: 26px; height: 26px; flex: none; }
</style>
</head>
<body>
<main class="canvas">
  <section class="card" aria-label="Business card for 412 Silver Hawk Detailing">
    <header class="brand-band">
      <h1 class="brand-name">412 Silver Hawk Detailing</h1>
    </header>
    <div class="squeegee-art" role="img" aria-label="Illustration of a window squeegee with a dark blade and green handle"></div>
    <h2 class="owner-name">Dale Marsh</h2>
    <ul class="services">
      <li class="service">
        <svg class="service-icon" viewBox="0 0 26 26" aria-hidden="true">
          <circle cx="13" cy="13" r="8" fill="none" stroke="#111" stroke-width="1.5"/>
          <circle cx="13" cy="13" r="3.5" fill="#111"/>
          <path d="M13 1v6M13 19v6M1 13h6M19 13h6" stroke="#111" stroke-width="1.5"/>
        </svg>
        Window Cleaning
      </li>
      <li class="service">
        <svg class="service-icon" viewBox="0 0 26 26" aria-hidden="true">
          <circle cx="13" cy="13" r="8" fill="none" stroke="#111" stroke-width="1.5"/>
          <circle cx="13" cy="13" r="3.5" fill="#111"/>
          <path d="M13 1v6M13 19v6M1 13h6M19 13h6" stroke="#111" stroke-width="1.5"/>
        </svg>
        House Maintenance
      </li>
    </ul>
  </section>
</main>
</body>
</html>
```